Rig up a website for a Rigging Company

We already have a logo. Looking for a website design that works on pavlune.com.
Our rigging company uses semi trucks, forklifts, and similar equipment to move large machines.
Our logo is white, black and red.

Target Market(s)

Medical Industry (moving medical equipment), Utility Industry (power equipment), Food Industry (moving bottling/packing equipment), US Government (large equipment)

Industry/Entity Type

It Company

Coding

Coded - Design and coding required

Number of Pages Required

5+ page

Font styles to use
Sans Serif

Colors
ec1f27
ffffff
0355a3

Requirements
Must have
• Home page, About page, Services Page, and Contact Information page
Nice to have
• Pictures of semi and forklifts and ability to insert our own pictures of our equipment

```html
<!DOCTYPE html>
<html lang="en">
<head>
<meta charset="utf-8">
<title>Halden Rigging</title>
<link href="https://fonts.googleapis.com/css2?family=Montserrat:wght@400;600;700;800&family=Open+Sans:wght@400;600&display=swap" rel="stylesheet">
<style>
:root{
  --red:#e31e24;
  --ink:#1d1d1f;
  --text:#444;
  --muted:#666;
  --grey-band:#e9e9eb;
  --white:#fff;
  --blue:#0355a3;
  --social-1:#3b5998;
  --social-2:#1da1f2;
  --social-3:#dd4b39;
  --social-4:#0077b5;
  --line:#dcdcdc;
}
*{box-sizing:border-box;margin:0;padding:0}
html,body{width:1200px;height:4000px;overflow:hidden;background:var(--white)}
body{font-family:"Open Sans",Arial,sans-serif;color:var(--text);position:relative}
.abs{position:absolute}
.heading{font-family:"Montserrat",Arial,sans-serif}

/* header */
.site-header{position:absolute;left:0;top:0;width:1200px;height:138px}
.brand{position:absolute;display:flex;align-items:center;gap:12px;font-family:"Montserrat",Arial,sans-serif;font-weight:800;color:var(--ink);letter-spacing:1px}
.brand-mark{width:30px;height:30px;background:var(--red)}
.site-header .brand{left:133px;top:30px;font-size:34px}
.connect{position:absolute;left:718px;top:26px;font-family:"Montserrat",sans-serif;font-size:11px;font-weight:700;color:var(--ink);letter-spacing:.5px}
.socials{display:flex;gap:5px}
.socials span{width:20px;height:20px;display:block}
.socials span:nth-child(1){background:var(--social-1)}
.socials span:nth-child(2){background:var(--social-2)}
.socials span:nth-child(3){background:var(--social-3)}
.socials span:nth-child(4){background:var(--social-4)}
.connect .socials{margin-top:8px}
.call{position:absolute;left:878px;top:26px;display:flex;gap:12px;align-items:flex-start}
.call small{display:block;font-family:"Montserrat",sans-serif;font-size:11px;font-weight:700;color:var(--ink)}
.call strong{display:block;font-family:"Montserrat",sans-serif;font-size:22px;font-weight:600;color:var(--red);margin-top:4px}
.main-nav{position:absolute;left:483px;top:96px;display:flex;gap:14px;font-family:"Montserrat",sans-serif;font-size:13px;font-weight:700;color:var(--ink)}
.main-nav a{padding:6px 10px;color:inherit;text-decoration:none}
.main-nav a.active{background:var(--red);color:var(--white)}

/* hero */
.hero{position:absolute;left:0;top:138px;width:1200px;height:572px;background:linear-gradient(180deg,#3f79bd 0%,#8fb6e0 45%,#c9b06c 78%,#8e7a55 100%)}
.hero-title{position:absolute;left:724px;top:88px;font-family:"Montserrat",sans-serif;font-size:60px;font-weight:600;color:var(--white);letter-spacing:1px}
.hero-sub{position:absolute;left:726px;top:170px;font-size:20px;color:var(--white);font-weight:600}
.btn-solid{position:absolute;background:var(--red);color:var(--white);font-family:"Montserrat",sans-serif;font-weight:600;display:flex;align-items:center;justify-content:center;gap:10px}
.hero .btn-solid{left:726px;top:224px;width:174px;height:54px;font-size:16px}
.dots{position:absolute;left:540px;top:510px;display:flex;gap:12px}
.dots i{width:10px;height:10px;border-radius:50%;background:var(--white);display:block;opacity:.85}
.dots i:first-child{background:transparent;border:2px solid var(--white)}

/* welcome */
.section-title{position:absolute;width:1200px;left:0;text-align:center;font-family:"Montserrat",sans-serif;font-weight:600;color:var(--red);font-size:27px}
.section-lead{position:absolute;width:1200px;left:0;text-align:center;font-size:16px;line-height:28px;color:var(--text)}
.service{position:absolute;width:220px;text-align:center;top:928px}
.service-icon{width:150px;height:150px;border-radius:50%;background:var(--red);margin:0 auto;display:flex;align-items:center;justify-content:center}
.service-name{margin-top:38px;font-family:"Montserrat",sans-serif;font-weight:700;font-size:16px;line-height:22px;color:var(--red)}

/* banner */
.banner{position:absolute;left:168px;top:1221px;width:867px;height:414px;background:linear-gradient(160deg,#7aa5d4 0%,#9a4a3c 40%,#b43a2f 60%,#c9a23a 85%,#7b7465 100%)}
.banner-box{position:absolute;left:507px;top:38px;width:330px;height:154px;background:rgba(20,30,45,.88);padding:22px 22px}
.banner-box p{font-family:"Montserrat",sans-serif;font-size:21px;font-weight:600;color:var(--white);line-height:30px}
.banner-box p em{font-style:normal;color:var(--red);font-size:26px}
.banner-box .btn-light{margin-top:12px;background:var(--white);color:var(--ink);font-family:"Montserrat",sans-serif;font-weight:600;font-size:14px;height:42px;display:flex;align-items:center;justify-content:center}
.banner .btn-solid{left:677px;top:227px;width:158px;height:48px;font-size:15px}

/* projects */
.projects{position:absolute;left:0;top:1707px;width:1200px;height:960px;background:var(--grey-band)}
.project{position:absolute;width:298px;text-align:center}
.project-photo{width:298px;height:192px}
.project h3{font-family:"Montserrat",sans-serif;font-size:17px;font-weight:700;color:var(--red);margin-top:26px}
.project p{font-size:13px;line-height:20px;color:var(--text);margin-top:8px}
.btn-outline{display:inline-flex;align-items:center;justify-content:center;border:1.5px solid var(--red);color:var(--red);font-family:"Montserrat",sans-serif;font-size:11px;font-weight:600;width:104px;height:32px;background:var(--white)}
.project .btn-outline{margin-top:18px}

/* blog */
.blog-title{position:absolute;left:133px;top:2750px;font-family:"Montserrat",sans-serif;font-size:27px;font-weight:600;color:var(--red)}
.blog-all{left:909px;top:2744px;width:158px;height:42px;font-size:14px}
.post{position:absolute;top:2835px;width:298px;height:365px;background:var(--white);box-shadow:0 2px 14px rgba(0,0,0,.18);padding:24px 21px}
.post-photo{width:256px;height:138px}
.post h4{font-family:"Open Sans",sans-serif;font-weight:400;font-size:18px;line-height:27px;color:var(--ink);margin-top:20px}
.post p{font-size:12px;line-height:19px;color:var(--text);margin-top:12px}
.post .btn-outline{margin-top:20px}

/* cta */
.cta{position:absolute;left:0;top:3275px;width:1200px;height:285px;background:var(--grey-band)}
.cta .btn-solid{left:491px;top:162px;width:216px;height:56px;font-size:19px}

/* footer */
.site-footer{position:absolute;left:0;top:3560px;width:1200px;height:440px}
.site-footer .brand{left:133px;top:110px;font-size:34px}
.foot-label{position:absolute;font-family:"Montserrat",sans-serif;font-size:12px;font-weight:700;color:var(--red)}
.foot-menu{position:absolute;left:584px;top:115px;list-style:none;font-size:12px;line-height:25.5px;color:var(--ink)}
.contact-row{position:absolute;left:866px;display:flex;gap:20px;font-size:12px;line-height:21px;color:var(--ink)}
.foot-rule{position:absolute;left:133px;top:341px;width:934px;height:1px;background:var(--line)}
.copyright{position:absolute;left:0;width:1200px;top:384px;text-align:center;font-size:11px;color:var(--ink)}
</style>
</head>
<body>

<header class="site-header">
  <div class="brand"><span class="brand-mark"></span>HALDEN RIGGING</div>
  <div class="connect">CONNECT WITH US
    <div class="socials"><span></span><span></span><span></span><span></span></div>
  </div>
  <div class="call">
    <svg width="26" height="26" viewBox="0 0 24 24"><path fill="#e31e24" d="M6.6 10.8a15 15 0 0 0 6.6 6.6l2.2-2.2a1 1 0 0 1 1-.25 11.4 11.4 0 0 0 3.6.57 1 1 0 0 1 1 1V20a1 1 0 0 1-1 1A17 17 0 0 1 3 4a1 1 0 0 1 1-1h3.5a1 1 0 0 1 1 1c0 1.25.2 2.45.57 3.57a1 1 0 0 1-.25 1z"/></svg>
    <div><small>CALL US TODAY!</small><strong>(555) 014.2290</strong></div>
  </div>
  <nav class="main-nav">
    <a class="active">HOME</a><a>ABOUT US</a><a>SERVICES</a><a>PROJECTS</a><a>OUR EQUIPMENT</a><a>CONTACT US</a>
  </nav>
</header>

<section class="hero" role="img" aria-label="Yellow mobile crane lifting a steel beam on a construction site under a blue sky">
  <div class="hero-title">RIGGING</div>
  <div class="hero-sub">Lorem Ipsum is simply dummy text</div>
  <div class="btn-solid">READ MORE <svg width="10" height="12" viewBox="0 0 10 12"><path d="M1 0l8 6-8 6z" fill="#fff"/></svg></div>
  <div class="dots"><i></i><i></i><i></i><i></i><i></i></div>
</section>

<h2 class="section-title" style="top:768px">WELCOME TO OUR SITE</h2>
<p class="section-lead" style="top:826px">There are many variations of passages of Lorem Ipsum available, but the majority<br>have suffered alteration in some form, by injected humour.</p>

<div class="service" style="left:183px">
  <div class="service-icon"><svg width="86" height="60" viewBox="0 0 86 60" fill="none" stroke="#fff" stroke-width="4"><rect x="4" y="8" width="50" height="34"/><path d="M54 20h16l12 12v10H54z"/><circle cx="18" cy="48" r="7" fill="#e31e24"/><circle cx="66" cy="48" r="7" fill="#e31e24"/></svg></div>
  <div class="service-name">HEAVY<br>HAULING</div>
</div>
<div class="service" style="left:383px">
  <div class="service-icon"><svg width="70" height="76" viewBox="0 0 70 76" fill="none" stroke="#fff" stroke-width="4"><path d="M35 2v12M22 26l13-12 13 12"/><rect x="6" y="26" width="58" height="44"/><path d="M18 30v36M29 30v36M41 30v36M52 30v36"/></svg></div>
  <div class="service-name">RIGGING<br>EQUIPMENT</div>
</div>
<div class="service" style="left:589px">
  <div class="service-icon"><svg width="80" height="76" viewBox="0 0 80 76" fill="none" stroke="#fff" stroke-width="4"><path d="M10 50L56 6l14 6M62 10v20"/><path d="M58 30h8v6h-8z" fill="#fff"/><rect x="6" y="46" width="44" height="12"/><rect x="4" y="60" width="54" height="10" rx="5"/></svg></div>
  <div class="service-name">CRANE<br>RENTAL</div>
</div>
<div class="service" style="left:797px">
  <div class="service-icon"><svg width="80" height="70" viewBox="0 0 80 70" fill="none" stroke="#fff" stroke-width="4"><path d="M14 10h20l8 24v18H10V30h24"/><path d="M52 4v52h24"/><rect x="22" y="40" width="10" height="8"/><circle cx="20" cy="58" r="7" fill="#e31e24"/><circle cx="40" cy="58" r="7" fill="#e31e24"/></svg></div>
  <div class="service-name">MACHINERY<br>MOVING</div>
</div>

<section class="banner" role="img" aria-label="Reach stacker forklift lifting a red shipping container in a port yard">
  <div class="banner-box">
    <p>OUR RIGGING COMPANY<br>USES <em>FORKLIFTS</em></p>
    <div class="btn-light">VIEW OUR EQUIPMENT LISTINGS</div>
  </div>
  <div class="btn-solid">GET A QUOTE</div>
</section>

<section class="projects">
  <h2 class="section-title" style="top:54px">OUR PROJECTS</h2>
  <p class="section-lead" style="top:104px;font-size:15px">There are many variations of passages of Lorem Ipsum available</p>

  <div class="project" style="left:131px;top:176px"><div class="project-photo" role="img" aria-label="Yellow truck crane on a site" style="background:linear-gradient(180deg,#7fb1e0,#c7c05a 70%,#6f7c3a)"></div><h3>HEADING 1</h3><p>There are many variations of passages<br>of Lorem Ipsum available</p><span class="btn-outline">READ MORE</span></div>
  <div class="project" style="left:451px;top:176px"><div class="project-photo" role="img" aria-label="Container handler lifting a red container" style="background:linear-gradient(180deg,#4f86c2,#b9533f 55%,#6b6e75)"></div><h3>HEADING 2</h3><p>There are many variations of passages<br>of Lorem Ipsum available</p><span class="btn-outline">READ MORE</span></div>
  <div class="project" style="left:771px;top:176px"><div class="project-photo" role="img" aria-label="Forklift moving cargo beside containers" style="background:linear-gradient(160deg,#8cb6d8,#d08a3c 55%,#9a4530)"></div><h3>HEADING 3</h3><p>There are many variations of passages<br>of Lorem Ipsum available</p><span class="btn-outline">READ MORE</span></div>

  <div class="project" style="left:131px;top:560px"><div class="project-photo" role="img" aria-label="Blue mobile crane at a work yard" style="background:linear-gradient(180deg,#bcd4ea,#3c6ea8 60%,#5d6169)"></div><h3>HEADING 4</h3><p>There are many variations of passages<br>of Lorem Ipsum available</p><span class="btn-outline">READ MORE</span></div>
  <div class="project" style="left:451px;top:560px"><div class="project-photo" role="img" aria-label="Red gantry cranes at a port" style="background:linear-gradient(180deg,#9cc3e6,#d9e6f2 55%,#c9473a 80%,#7b8087)"></div><h3>HEADING 5</h3><p>There are many variations of passages<br>of Lorem Ipsum available</p><span class="btn-outline">READ MORE</span></div>
  <div class="project" style="left:771px;top:560px"><div class="project-photo" role="img" aria-label="Crane beside steel building frame" style="background:linear-gradient(180deg,#a8c3dc,#c9b36a 60%,#77705e)"></div><h3>HEADING 6</h3><p>There are many variations of passages<br>of Lorem Ipsum available</p><span class="btn-outline">READ MORE</span></div>
</section>

<h2 class="blog-title">LATEST BLOG</h2>
<div class="btn-solid blog-all">VIEW ALL BLOGS</div>

<article class="post" style="left:131px"><div class="post-photo" role="img" aria-label="White truck with loading crane" style="background:linear-gradient(180deg,#d7dde3,#eef0f2 50%,#8a8f96)"></div><h4>There are many variations of passages of Lorem</h4><p>It is a long established fact that a reader will be distracted by the readable.</p><span class="btn-outline">READ MORE</span></article>
<article class="post" style="left:451px"><div class="post-photo" role="img" aria-label="Forklift inside a warehouse aisle" style="background:linear-gradient(180deg,#3f3a3a,#b0342c 50%,#6b6b70)"></div><h4>It is a long established fact that a reader will be</h4><p>It is a long established fact that a reader will be distracted by the readable.</p><span class="btn-outline">READ MORE</span></article>
<article class="post" style="left:771px"><div class="post-photo" role="img" aria-label="Orange pallet stacker in a bright warehouse" style="background:linear-gradient(180deg,#c9ccd0,#9ea3a8 55%,#d48a2e 80%,#a0a4a8)"></div><h4>It uses a dictionary of over atin words combined.</h4><p>It is a long established fact that a reader will be distracted by the readable.</p><span class="btn-outline">READ MORE</span></article>

<section class="cta">
  <h2 class="section-title" style="top:54px">IT'S LARGEST RIGGING COMPANY</h2>
  <p class="section-lead" style="top:102px;font-size:15px">It is a long established fact that a reader will be distracted by the readable</p>
  <div class="btn-solid">GET STARTED</div>
</section>

<footer class="site-footer">
  <div class="brand"><span class="brand-mark"></span>HALDEN RIGGING</div>
  <div class="foot-label" style="left:197px;top:218px">CONNECT WITH US</div>
  <div class="socials abs" style="left:191px;top:255px"><span style="width:26px;height:26px"></span><span style="width:26px;height:26px"></span><span style="width:26px;height:26px"></span><span style="width:26px;height:26px"></span></div>

  <div class="foot-label" style="left:584px;top:72px">MENU</div>
  <ul class="foot-menu"><li>Home</li><li>About Us</li><li>Services</li><li>Projects</li><li>Our Equipment</li><li>Blog</li><li>Contact us</li></ul>

  <div class="foot-label" style="left:864px;top:72px">CONTACT US</div>
  <div class="contact-row" style="top:118px"><svg width="14" height="18" viewBox="0 0 14 18"><path d="M7 0a7 7 0 0 0-7 7c0 5 7 11 7 11s7-6 7-11a7 7 0 0 0-7-7zm0 10a3 3 0 1 1 0-6 3 3 0 0 1 0 6z" fill="#1d1d1f"/></svg><span>48 Millbrook Lane<br>Ashford, CT 06278</span></div>
  <div class="contact-row" style="top:192px"><svg width="14" height="14" viewBox="0 0 24 24"><path fill="#1d1d1f" d="M6.6 10.8a15 15 0 0 0 6.6 6.6l2.2-2.2a1 1 0 0 1 1-.25 11.4 11.4 0 0 0 3.6.57 1 1 0 0 1 1 1V20a1 1 0 0 1-1 1A17 17 0 0 1 3 4a1 1 0 0 1 1-1h3.5a1 1 0 0 1 1 1c0 1.25.2 2.45.57 3.57a1 1 0 0 1-.25 1z"/></svg><span>(555) 014.2290</span></div>
  <div class="contact-row" style="top:240px"><svg width="15" height="12" viewBox="0 0 15 12"><rect width="15" height="12" fill="#1d1d1f"/><path d="M0 0l7.5 6L15 0" stroke="#fff" stroke-width="1.5" fill="none"/></svg><span>info@pavlune.com</span></div>

  <div class="foot-rule"></div>
  <p class="copyright">Copyright © 2017 All Rights Reserved</p>
</footer>

</body>
</html>
```